Veldmark Supplies Business Card

Professional business card that stand out to our potential customers. Front and back with clean modern design

Industry/Entity Type

Oil and gas

Contact Information for Business Card

Name, address, website , office phone and cell number

Requirements
Must have
• Editable files for each employee

```html
<!DOCTYPE html>
<html lang="en">
<head>
<meta charset="utf-8">
<title>Veldmark Supplies Business Card</title>
<link rel="stylesheet" href="https://fonts.googleapis.com/css2?family=Exo+2:wght@400;800&display=swap">
<style>
  :root {
    --backdrop: #2b2b2d;
    --card: #1c1c1e;
    --card-edge: #111113;
    --red: #ff1a12;
    --cyan: #1eb4dc;
    --ink: #e6e6e8;
    --rule: #cfcfd2;
  }
  * { margin: 0; padding: 0; box-sizing: border-box; }
  html, body {
    width: 1200px; height: 694px; overflow: hidden;
    background: var(--backdrop);
    font-family: "Exo 2", sans-serif;
  }
  .stage { position: relative; width: 1200px; height: 694px; }
  .card {
    position: absolute; top: 192px;
    width: 540px; height: 310px;
    border-radius: 22px;
    background: var(--card);
    box-shadow: 0 14px 30px rgba(0,0,0,.45);
    overflow: hidden;
  }
  .card--back { left: 40px; }
  .card--front { left: 620px; }

  .back-pattern {
    position: absolute; inset: 0;
    background: radial-gradient(circle at 60% 45%, #262628 0%, #19191b 70%, #121214 100%);
  }
  .back-brand {
    position: absolute; left: 0; right: 0; top: 140px;
    text-align: center;
    font-weight: 800; font-size: 24px; color: var(--red);
  }

  .brand {
    position: absolute; right: 30px; top: 98px;
    display: flex; align-items: center; gap: 8px;
  }
  .brand-square { width: 14px; height: 14px; background: var(--cyan); }
  .brand-name { font-weight: 800; font-size: 22px; color: var(--red); }

  .person { position: absolute; left: 30px; top: 104px; }
  .person-name { font-weight: 800; font-size: 26px; color: var(--red); line-height: 1; }
  .person-role { font-weight: 400; font-size: 15px; color: var(--cyan); margin-top: 6px; }

  .divider {
    position: absolute; left: 30px; right: 30px; top: 168px;
    height: 1px; background: var(--rule);
  }

  .contacts { position: absolute; top: 186px; list-style: none; }
  .contacts li {
    display: flex; align-items: center; gap: 12px;
    height: 25px; font-size: 14px; color: var(--ink);
  }
  .contacts svg { width: 16px; height: 16px; flex: none; fill: var(--cyan); }
  .contacts--left { left: 30px; }
  .contacts--right { right: 30px; text-align: right; }
  .contacts--right li { justify-content: flex-end; }
  .contacts--right .icon-slot { width: 16px; flex: none; }
</style>
</head>
<body>
<main class="stage">
  <section class="card card--back" aria-label="Card back">
    <div class="back-pattern" role="img" aria-label="Dark embossed repeating brand pattern"></div>
    <div class="back-brand">Veldmark Supplies</div>
  </section>

  <section class="card card--front" aria-label="Card front">
    <div class="brand">
      <span class="brand-square"></span>
      <span class="brand-name">Veldmark Supplies</span>
    </div>

    <div class="person">
      <div class="person-name">Daniel Harlow</div>
      <div class="person-role">Owner</div>
    </div>

    <div class="divider"></div>

    <ul class="contacts contacts--left">
      <li>
        <svg viewBox="0 0 24 24" aria-hidden="true"><path d="M6.6 10.8a15 15 0 0 0 6.6 6.6l2.2-2.2a1 1 0 0 1 1-.25 11.4 11.4 0 0 0 3.6.57 1 1 0 0 1 1 1V20a1 1 0 0 1-1 1A17 17 0 0 1 3 4a1 1 0 0 1 1-1h3.5a1 1 0 0 1 1 1c0 1.25.2 2.45.57 3.6a1 1 0 0 1-.25 1z"/></svg>
        <span>072-418 390 255</span>
      </li>
      <li>
        <svg viewBox="0 0 24 24" aria-hidden="true"><path d="M7 1h10a2 2 0 0 1 2 2v18a2 2 0 0 1-2 2H7a2 2 0 0 1-2-2V3a2 2 0 0 1 2-2zm0 3v15h10V4zm5 16.2a1 1 0 1 0 0 .1z"/></svg>
        <span>072-418 390 266</span>
      </li>
      <li>
        <svg viewBox="0 0 24 24" aria-hidden="true"><path d="M2 5h20v14H2zm2 2v.5l8 5 8-5V7z"/></svg>
        <span>office@veldmark.net</span>
      </li>
    </ul>

    <ul class="contacts contacts--right">
      <li>
        <span>www.veldmarksupply.net</span>
        <svg viewBox="0 0 24 24" aria-hidden="true"><path d="M12 2a10 10 0 1 0 0 20 10 10 0 0 0 0-20zm6.9 6h-3a15 15 0 0 0-1.3-3.9A8 8 0 0 1 18.9 8zM12 4c.8 1.1 1.5 2.5 1.9 4h-3.8c.4-1.5 1.1-2.9 1.9-4zM4.3 14a8 8 0 0 1 0-4h3.4a16 16 0 0 0 0 4zm.8 2h3a15 15 0 0 0 1.3 3.9A8 8 0 0 1 5.1 16zM8 8H5.1a8 8 0 0 1 4.3-3.9A15 15 0 0 0 8 8zm4 12c-.8-1.1-1.5-2.5-1.9-4h3.8c-.4 1.5-1.1 2.9-1.9 4zm2.3-6H9.7a14 14 0 0 1 0-4h4.6a14 14 0 0 1 0 4zm.3 5.9A15 15 0 0 0 16 16h3a8 8 0 0 1-4.4 3.9zM16.3 14a16 16 0 0 0 0-4h3.4a8 8 0 0 1 0 4z"/></svg>
      </li>
      <li>
        <span>318, Ridgeway Field Road</span>
        <svg viewBox="0 0 24 24" aria-hidden="true"><path d="M12 2a7 7 0 0 0-7 7c0 5.2 7 13 7 13s7-7.8 7-13a7 7 0 0 0-7-7zm0 9.5a2.5 2.5 0 1 1 0-5 2.5 2.5 0 0 1 0 5z"/></svg>
      </li>
      <li>
        <span>79705, Basin County</span>
        <span class="icon-slot"></span>
      </li>
    </ul>
  </section>
</main>
</body>
</html>
```